QVR business card

Need a business card for a company that provides instructional design and elearning development services. The website is here: http://quorvane.studio/

I'm attaching a current logo, as well as the old business card design. While I like to keep it clean, the old design is too simplistic for my liking. The only idea I want to reuse from the old design is placing industry jargon on the back of the card, just need a better way to present it. But if you have other ideas for the back--feel free to experiment.

Please use the colors complementary to the color we have on the website. Thank you!

```html
<!DOCTYPE html>
<html lang="en">
<head>
<meta charset="utf-8">
<title>QVR business card</title>
<link rel="stylesheet" href="https://fonts.googleapis.com/css2?family=Varela+Round&family=Open+Sans:wght@400;600;700&family=Roboto:wght@700;900&display=swap">
<style>
  :root{
    --teal:#1fae98;
    --teal-light:#5fd0bd;
    --ink:#111;
    --text-dark:#333;
    --paper:#ffffff;
    --paper-shade:#dcdcdc;
    --backdrop:#2b2b2b;
    --white:#fff;
  }
  html,body{margin:0;padding:0;width:1200px;height:997px;overflow:hidden;background:var(--backdrop);}
  .canvas{position:relative;width:1200px;height:997px;}
  .card{position:absolute;width:620px;height:354px;border-radius:14px;overflow:hidden;box-shadow:0 18px 40px rgba(0,0,0,.55);}
  .card svg.shapes{position:absolute;inset:0;}
  .card-front{left:110px;top:90px;background:linear-gradient(160deg,var(--paper) 40%,var(--paper-shade));}
  .card-back{left:470px;top:540px;}

  .brand{position:absolute;font-family:"Varela Round",sans-serif;color:var(--teal);display:flex;align-items:center;gap:10px;}
  .brand .dot{width:16px;height:16px;background:var(--ink);border-radius:50%;}
  .brand-name{font-size:58px;line-height:1;}
  .card-front .brand{left:200px;top:110px;}
  .tagline{position:absolute;left:226px;top:178px;font-family:"Open Sans",sans-serif;font-size:13px;color:var(--text-dark);}
  .holder{position:absolute;right:26px;top:176px;text-align:right;font-family:"Open Sans",sans-serif;transform:translateY(-100px);}
  .holder-name{font-size:16px;font-weight:700;color:var(--text-dark);}
  .holder-role{font-size:13px;color:var(--teal);}
  .contact{position:absolute;left:22px;bottom:18px;font-family:"Open Sans",sans-serif;font-size:13px;color:var(--teal);line-height:1.9;}
  .contact span{display:flex;align-items:center;gap:8px;}
  .contact svg{width:13px;height:13px;fill:#bbb;}

  .card-back .brand{left:28px;top:38px;}
  .card-back .brand-name{font-size:46px;}
  .service{position:absolute;font-family:"Roboto",sans-serif;font-weight:900;font-size:12px;line-height:1.15;color:var(--ink);text-align:center;text-transform:uppercase;}
  .visit{position:absolute;right:22px;bottom:26px;text-align:right;font-family:"Open Sans",sans-serif;}
  .visit-lead{font-size:16px;color:var(--teal);}
  .visit-url{font-size:15px;color:var(--white);font-weight:600;}
</style>
</head>
<body>
<div class="canvas">

  <section class="card card-front" aria-label="Card front">
    <svg class="shapes" width="620" height="354" viewBox="0 0 620 354">
      <path d="M0 262 C190 225 380 215 620 92 L620 354 L0 354Z" fill="var(--teal-light)"/>
      <path d="M0 276 C190 240 380 230 620 108 L620 354 L0 354Z" fill="var(--teal)"/>
      <path d="M0 292 C190 258 380 248 620 126 L620 354 L0 354Z" fill="var(--ink)"/>
    </svg>
    <div class="brand"><span class="dot"></span><span class="brand-name">QVR</span></div>
    <div class="tagline">Ready to take your learning on the go?</div>
    <div class="holder">
      <div class="holder-name">Marek Toliver</div>
      <div class="holder-role">Owner</div>
    </div>
    <div class="contact">
      <span><svg viewBox="0 0 24 24"><path d="M6.6 10.8a15 15 0 0 0 6.6 6.6l2.2-2.2c.3-.3.7-.4 1-.2 1.1.4 2.3.6 3.6.6.6 0 1 .4 1 1V20c0 .6-.4 1-1 1A17 17 0 0 1 3 4c0-.6.4-1 1-1h3.5c.6 0 1 .4 1 1 0 1.3.2 2.5.6 3.6.1.3 0 .7-.2 1z"/></svg>646-555-0187</span>
      <span><svg viewBox="0 0 24 24"><path d="M2 5h20v14H2z M2 5l10 8 10-8" fill="#bbb" stroke="#111" stroke-width="1.5"/></svg>mtoliver@quorvane.studio</span>
    </div>
  </section>

  <section class="card card-back" aria-label="Card back">
    <svg class="shapes" width="620" height="354" viewBox="0 0 620 354">
      <defs>
        <linearGradient id="photoTone" x1="0" y1="0" x2="1" y2="1">
          <stop offset="0" stop-color="#d9dde0"/>
          <stop offset=".55" stop-color="#a9b2b8"/>
          <stop offset="1" stop-color="#e6e6e6"/>
        </linearGradient>
      </defs>
      <rect width="620" height="354" fill="url(#photoTone)" role="img" aria-label="Collage of business and learning photos with a man in a suit and tie"/>
      <path d="M0 288 C200 292 360 240 470 180 S590 128 620 126 L620 354 L0 354Z" fill="var(--teal-light)"/>
      <path d="M0 300 C200 304 360 252 470 192 S590 140 620 138 L620 354 L0 354Z" fill="var(--teal)"/>
      <path d="M0 318 C210 322 370 270 480 212 S595 160 620 158 L620 354 L0 354Z" fill="var(--ink)"/>
      <g fill="var(--teal)" stroke="#e8e8e8" stroke-width="4">
        <circle cx="130" cy="300" r="34"/>
        <circle cx="290" cy="272" r="34"/>
        <circle cx="430" cy="216" r="34"/>
        <circle cx="565" cy="150" r="34"/>
      </g>
      <g fill="#fff">
        <path d="M118 290h10a5 5 0 1 1 8 0h8v10a5 5 0 1 0 0 8v8h-26z"/>
        <path d="M276 264h22v14a6 6 0 0 1-6 6h-10a6 6 0 0 1-6-6z M298 268h4a4 4 0 0 1 0 8h-4v-3h3a1 1 0 0 0 0-2h-3z"/>
        <path d="M418 226a9 9 0 0 1 1-18 11 11 0 0 1 21 3 8 8 0 0 1 1 15z" />
        <path d="M553 141h6l2-4h8l2 4h6v20h-24z"/>
      </g>
      <path d="M430 222v-10m-5 5l5-6 5 6" stroke="var(--teal)" stroke-width="2.5" fill="none"/>
      <circle cx="565" cy="151" r="5" fill="var(--teal)"/>
    </svg>
    <div class="brand"><span class="dot"></span><span class="brand-name">QVR</span></div>
    <div class="service" style="left:68px;top:232px;width:124px;">Instructional<br>Design</div>
    <div class="service" style="left:222px;top:204px;width:136px;">E-Learning<br>Development</div>
    <div class="service" style="left:380px;top:150px;width:100px;">Mobile<br>Learning</div>
    <div class="service" style="left:505px;top:84px;width:120px;">Instructor-Led<br>Training</div>
    <div class="visit">
      <div class="visit-lead">Visit us on</div>
      <div class="visit-url">www.quorvane.studio</div>
    </div>
  </section>

</div>
</body>
</html>
```